Commercial Real Estate for Lease Listing Flyer

I am looking to put together a flyer for our available office space in our building. It needs to look professional and it will be standard sized 8.5 x 11 and double sided. Full color as well. This flyer will need to be able to be put in a PDF and a picture file that can be embedded in an email. I have included pictures, logo, and a Word document with the information you should need. Also, I included a bunch of SAMPLE leasing flyers that you can get ideas from. The floor plan is also included in here. I want it specifically noted that the top suite is Suite 100 and the bottom suite is 120. And list their size as well. I will be reviewing all designs very quickly, so be sure to check the comments.

• Please refer to these links for additional photos:
• "Twilight 1.jpg" at: https://files.plinthdocs.net/a/preview/3f7d1a92-b4e0-4c1a-8e5f-71c0d2ab9e34
• Twilight 2_straightened.jpg" at: https://files.plinthdocs.net/a/preview/a15c8e03-7d2b-4f9e-b6a1-0c93e4f72d58
• "Twilight 3.jpg" at: https://files.plinthdocs.net/a/preview/6e2b9f71-c3a4-4d08-9e7b-5f1a8c03d6e2
• "Twilight 4.jpg" at: https://files.plinthdocs.net/a/preview/c84a0d6e-1f3b-4e57-a2c9-9b7e05f4d813
• "Twilight 5.jpg" at: https://files.plinthdocs.net/a/preview/7b0f5c28-e6d1-4a93-8f4e-d25a1b6c07f9
• "Twilight 6.jpg" at: https://files.plinthdocs.net/a/preview/e3c6a417-5b92-4f0d-bc8e-4a1f97d2e065
• "Twilight 7.jpg" at: https://files.plinthdocs.net/a/preview/5a9d2e80-c7f4-4b16-93a0-e8b6f1c4d27a
• "Twilight 8.jpg" at: https://files.plinthdocs.net/a/preview/b2e7f069-84c3-4d5a-a71e-3c0d9b58f6e4
• "Twilight 9.jpg" at: https://files.plinthdocs.net/a/preview/4d8c1b3f-a0e5-4f72-8b69-f17e2c05a9d3
• "Twilight 10.jpg" at: https://files.plinthdocs.net/a/preview/f09a6c52-3e18-4b7d-9c24-6b5d80e1f3a7
• "Twilight 11.jpg" at: https://files.plinthdocs.net/a/preview/8e4f2d06-b9c7-4a31-85e0-d7a3c16f4b92

```html
<!DOCTYPE html>
<html lang="en">
<head>
<meta charset="utf-8">
<title>Marlow Court Centre – Leasing Flyer</title>
<link rel="stylesheet" href="https://fonts.googleapis.com/css2?family=Marcellus&family=Arimo:wght@400;700&family=PT+Serif:ital@0;1&display=swap">
<style>
  :root{
    --ink:#111111;
    --paper:#ffffff;
    --stage:#e4e4e4;
    --gold:#d9bb7c;
    --gold-light:#ecd6a6;
    --gold-text:#c9a664;
    --amber:#9b7a3a;
    --mocha:#6b5440;
    --navy:#1f4e8c;
    --rule:#c9c9c9;
    --muted:#b6a48c;
  }
  *{box-sizing:border-box;margin:0;padding:0}
  html,body{width:1200px;height:1200px;overflow:hidden;background:var(--stage)}
  body{position:relative;font-family:"Arimo",Arial,sans-serif;color:var(--ink)}
  .page{position:absolute;background:var(--paper);overflow:hidden}
  .abs{position:absolute}

  /* ---------- back side ---------- */
  .flyer-back{left:32px;top:28px;width:544px;height:702px}
  .back-header{left:0;top:0;width:544px;height:54px;background:var(--ink);color:#fff;display:flex;align-items:center;justify-content:space-between;padding:0 20px 0 30px}
  .back-header .title{font-family:"Marcellus",serif;font-size:23px;white-space:nowrap;padding-top:3px}
  .back-header .address{font-size:8.2px;white-space:nowrap;padding-top:6px}

  .stats{left:38px;top:62px;font-size:8.6px;line-height:11px}
  .stats td{padding-right:4px;vertical-align:top}
  .divider{left:38px;width:150px;height:1px;background:var(--rule)}
  .rental{left:38px;top:110px}
  .rental h3{font-size:14.5px;font-weight:700}
  .rental .rate{font-size:14px;font-weight:700;margin-top:1px}
  .rental p{font-size:8px;line-height:10px}

  .features{left:38px;top:201px;width:186px}
  .features h3{font-size:14px;font-weight:700;color:var(--amber);margin-bottom:6px;white-space:nowrap}
  .features ul{list-style:none;font-size:9.2px;line-height:11px}
  .features li{position:relative;padding-left:14px;margin-bottom:2px}
  .features li svg{position:absolute;left:0;top:2px}

  .floor-plan{left:232px;top:60px;width:300px;height:282px;background:linear-gradient(135deg,#f6f6f6,#e6e6e6)}

  .overview{left:0;top:347px;width:220px;height:240px;background:var(--ink);color:#fff;padding:18px 20px 0 25px}
  .overview p{font-size:8.4px;line-height:11px;text-align:justify;font-weight:700}
  .overview hr{border:0;border-top:1px solid #555;margin:6px 0}

  .suites{left:220px;top:347px;width:324px;height:240px}
  .suite-band{position:absolute;left:0;width:324px;background:linear-gradient(100deg,var(--gold-light) 0%,var(--gold) 100%);border-bottom:1px solid #f4e8cf;padding:12px 0 0 20px}
  .suite-band h2{font-size:20px;font-weight:400;line-height:22px;white-space:nowrap}
  .suite-band h2 span{font-size:11.5px;font-weight:700}
  .suite-band p{font-size:11.5px;font-weight:700;line-height:15px;width:290px}
  .suite-band .combined{font-size:14px;font-weight:700;line-height:19px;margin-top:14px}

  .contact-footer{left:0;width:544px;height:116px;background:var(--paper)}
  .contact-footer .rule-top,.contact-footer .rule-bot{position:absolute;left:0;right:0;height:3px;background:linear-gradient(#e2e2e2,#c2c2c2)}
  .brand{position:absolute;font-family:"Marcellus",serif;color:var(--navy);text-align:center;line-height:1}
  .brand .name{font-size:31px;letter-spacing:3px}
  .brand .sub{font-size:13px;letter-spacing:4px;margin-top:4px}
  .contact{position:absolute;font-family:"PT Serif",serif}
  .contact .lead{font-family:"Arimo",sans-serif;font-weight:700;font-size:11.5px;letter-spacing:.3px}
  .contact .line{font-size:21px;line-height:28px;white-space:nowrap}
  .contact .line em{font-style:italic}
  .contact .email{color:var(--navy)}

  /* ---------- front side ---------- */
  .flyer-front{left:606px;top:440px;width:544px;height:706px}
  .front-header{left:0;top:0;width:544px;height:74px;background:var(--mocha);text-align:center;color:#fff}
  .front-header .title{margin-top:14px;font-family:"Marcellus",serif;font-size:40px;line-height:44px;white-space:nowrap}
  .front-header .address{font-size:8.5px;color:var(--muted);margin-top:-1px}
  .front-tagline{left:0;top:74px;width:544px;height:64px;background:var(--ink);text-align:center}
  .front-tagline .headline{font-weight:700;font-size:27px;color:var(--gold-text);line-height:30px;margin-top:6px;letter-spacing:.5px}
  .front-tagline .available{font-weight:700;font-size:17px;color:#fff;letter-spacing:14px;line-height:22px;padding-left:14px}
  .lobby-photo{left:0;top:138px;width:544px;height:334px;background:linear-gradient(100deg,#5a3a24 0%,#8a5a3a 30%,#c9b29a 60%,#e4dccf 80%,#b9b3aa 100%)}
  .accent-band{left:0;top:472px;width:544px;height:48px;background:var(--gold-light)}
  .thumb{top:438px;width:146px;height:124px;border:3px solid #fff;box-shadow:0 2px 3px rgba(0,0,0,.25)}
  .thumb-1{left:37px;background:linear-gradient(180deg,#d9c8a0 0%,#c9b48a 60%,#6f675d 100%)}
  .thumb-2{left:194px;background:linear-gradient(180deg,#cdb58a 0%,#e1d8c4 40%,#5b5249 100%)}
  .thumb-3{left:350px;background:linear-gradient(180deg,#ddd0b0 0%,#cbb894 60%,#7a6f62 100%)}
</style>
</head>
<body>

<section class="page flyer-back" aria-label="Flyer back side">
  <header class="abs back-header">
    <div class="title">MARLOW COURT CENTRE</div>
    <div class="address">4180 Marlow Court, Palm Harbor Gardens, FL 33400</div>
  </header>

  <table class="abs stats">
    <tr><td>Building Size</td><td>: 18,325 SF</td></tr>
    <tr><td>Vacant SF</td><td>: 3,791 SF</td></tr>
    <tr><td>Occupancy</td><td>: 79%</td></tr>
  </table>
  <div class="abs divider" style="top:102px"></div>

  <div class="abs rental">
    <h3>Rental Rate:</h3>
    <div class="rate">$32.00/SF</div>
    <p>plus suite electric<br>No extra operating expenses.</p>
  </div>
  <div class="abs divider" style="top:176px"></div>

  <div class="abs features">
    <h3>Features &amp; Amenities:</h3>
    <ul>
      <li><svg width="9" height="8" viewBox="0 0 9 8"><path d="M1 4l2.5 3L8 1" fill="none" stroke="#111" stroke-width="1.8"/></svg>Plenty of parking</li>
      <li><svg width="9" height="8" viewBox="0 0 9 8"><path d="M1 4l2.5 3L8 1" fill="none" stroke="#111" stroke-width="1.8"/></svg>On-site management</li>
      <li><svg width="9" height="8" viewBox="0 0 9 8"><path d="M1 4l2.5 3L8 1" fill="none" stroke="#111" stroke-width="1.8"/></svg>Some furniture available if needed.</li>
      <li><svg width="9" height="8" viewBox="0 0 9 8"><path d="M1 4l2.5 3L8 1" fill="none" stroke="#111" stroke-width="1.8"/></svg>Floor-to-ceiling hurricane impact windows throughout.</li>
      <li><svg width="9" height="8" viewBox="0 0 9 8"><path d="M1 4l2.5 3L8 1" fill="none" stroke="#111" stroke-width="1.8"/></svg>Completely move-in ready Change On site management to</li>
      <li><svg width="9" height="8" viewBox="0 0 9 8"><path d="M1 4l2.5 3L8 1" fill="none" stroke="#111" stroke-width="1.8"/></svg>On site ownership and management</li>
    </ul>
  </div>

  <div class="abs floor-plan" role="img" aria-label="Floor plan of Suites 100 and 120 showing offices, conference rooms, break room and reception"></div>

  <div class="abs overview">
    <p>The Marlow Court Centre is a beautiful Class A building situation in the heart of Palm Harbor Gardens but without the crazy Crestline traffic.</p>
    <hr>
    <p>Marlow Court Centre is located directly on I-95 just off of Marlow Court.</p>
    <hr>
    <p>The massive, new Harborview development south entrance is being built across the street. The building is very convenient to restaurants, shopping, and every other trade needed.</p>
    <hr>
    <p>The suites are incredibly well appointed and move-in ready with custom oak doors and millwork, 10' ceilings, floor to ceiling windows</p>
  </div>

  <div class="abs suites">
    <div class="suite-band" style="top:0;height:88px">
      <h2>Suite 100 <span>- 2,303 SF Available in February</span></h2>
      <p>2019 or earlier. 6 offices, break room, reception area, conference room, and a large meeting room.</p>
    </div>
    <div class="suite-band" style="top:88px;height:79px">
      <h2>Suite 120 <span>-1,488 SF Available Now. 2-3</span></h2>
      <p>offices, 1 large executive office, conference room, break room, and reception area.</p>
    </div>
    <div class="suite-band" style="top:167px;height:73px;padding-top:0">
      <p class="combined">BOTH SUITES CAN BE<br>COMBINED FOR 3,791 SF IN TOTAL.</p>
    </div>
  </div>

  <footer class="abs contact-footer" style="top:587px">
    <div class="rule-top" style="top:0"></div>
    <div class="brand" style="left:36px;top:32px"><div class="name">KESSEL</div><div class="sub">GROUP</div></div>
    <div class="contact" style="left:230px;top:12px">
      <div class="lead">FOR MORE INFORMATION, PLEASE CONTACT</div>
      <div class="line"><em>Dario Kessel</em> at 561-555-0142</div>
      <div class="line">or <span class="email">dario@kesselgroup.com</span></div>
    </div>
    <div class="rule-bot" style="top:92px"></div>
  </footer>
</section>

<section class="page flyer-front" aria-label="Flyer front side">
  <header class="abs front-header">
    <div class="title">MARLOW COURT CENTRE</div>
    <div class="address">4180 Marlow Court, Palm Harbor Gardens, FL 33400</div>
  </header>
  <div class="abs front-tagline">
    <div class="headline">CLASS A OFFICE SPACE</div>
    <div class="available">AVAILABLE</div>
  </div>
  <div class="abs lobby-photo" role="img" aria-label="Photo of the building lobby with wood-panelled walls, elevator, chandeliers and a console table"></div>
  <div class="abs accent-band"></div>
  <div class="abs thumb thumb-1" role="img" aria-label="Photo of a furnished private office with window"></div>
  <div class="abs thumb thumb-2" role="img" aria-label="Photo of an executive office with arched window and large desk"></div>
  <div class="abs thumb thumb-3" role="img" aria-label="Photo of an office with desk and wooden door"></div>

  <footer class="abs contact-footer" style="top:582px;height:124px">
    <div class="rule-top" style="top:8px"></div>
    <div class="brand" style="left:46px;top:30px"><div class="name">KESSEL</div><div class="sub">GROUP</div></div>
    <div class="contact" style="left:230px;top:18px">
      <div class="lead">FOR MORE INFORMATION, PLEASE CONTACT</div>
      <div class="line"><em>Dario Kessel</em> at 561-555-0142</div>
      <div class="line">or <span class="email">dario@kesselgroup.com</span></div>
    </div>
    <div class="rule-bot" style="top:92px"></div>
  </footer>
</section>

</body>
</html>
```